Satchel & Sundial needs new business card design

I need a new business card design. I'm looking for out-of-the-box design which represents the freedom of being a location independent entrepreneur.
I offer coaching, retreats and trips.
I would like to see designs with and without the photo.
Colors I use are black (#000000), green (#25A796) and brown (#D7C38C)
Website satchelandsundial.example

Target Market(s)

location independent entrepreneurs, digital nomads, people looking to swap the 9 to 5 for a lifestyle business

Industry/Entity Type

Business

Contact Information for Business Card

Dorota Falkner
Your Lifestyle Business Coach, Retreat & Trip Leader
http://satchelandsundial.example
hello@satchelandsundial.example
Live a life you don't need a holiday from

Font styles to use
Serif
Sans Serif

Requirements
Must have
• One side should contain only the logo. I would also consider having the "Live a life you don't need a holiday from" on that side too (depending on how it looks)
• Please show both sides on the designs.

```html
<!DOCTYPE html>
<html lang="en">
<head>
<meta charset="utf-8">
<title>Satchel &amp; Sundial — Business Card</title>
<link rel="stylesheet" href="https://fonts.googleapis.com/css2?family=Arimo:wght@400;700&display=swap">
<style>
  :root {
    --stage: #3a3a3c;
    --teal: #25a796;
    --teal-deep: #1c8c7d;
    --ink: #1b1b1b;
    --paper: #ffffff;
    --white-soft: rgba(255,255,255,0.85);
    --grey-text: #d9d9d9;
  }
  * { margin: 0; padding: 0; box-sizing: border-box; }
  html, body {
    width: 1200px; height: 843px; overflow: hidden;
    background: var(--stage);
    font-family: "Arimo", Arial, sans-serif;
  }
  .stage {
    position: relative; width: 1200px; height: 843px;
    display: flex; flex-direction: column; align-items: center; justify-content: center; gap: 40px;
  }
  .card {
    position: relative; width: 600px; height: 343px; overflow: hidden;
    box-shadow: 0 10px 30px rgba(0,0,0,0.35);
  }

  /* Back side: logo only */
  .card-back {
    background: linear-gradient(160deg, var(--teal) 0%, var(--teal-deep) 100%);
    display: flex; flex-direction: column; align-items: center; justify-content: center;
    color: var(--paper);
  }
  .brand-name {
    font-weight: 700; text-transform: uppercase; letter-spacing: 3px; white-space: nowrap;
  }
  .card-back .brand-name { font-size: 40px; color: var(--paper); }
  .card-back .divider {
    width: 360px; height: 1px; background: var(--white-soft); margin: 34px 0 18px;
  }
  .card-back .tagline { font-size: 15px; font-weight: 400; color: var(--white-soft); }

  /* Front side: contact details */
  .card-front { background: var(--paper); }
  .card-front .brand-name {
    position: absolute; left: 34px; top: 42px; font-size: 30px; color: var(--ink);
  }
  .card-front .swoosh { position: absolute; inset: 0; width: 600px; height: 343px; }
  .contact {
    position: absolute; right: 34px; bottom: 30px; text-align: right; color: var(--grey-text);
  }
  .contact .person { font-size: 20px; font-weight: 700; color: var(--teal); margin-bottom: 6px; }
  .contact .role { font-size: 15px; line-height: 1.3; color: var(--paper); }
  .contact .details { margin-top: 12px; font-size: 14px; line-height: 1.6; }
  .contact .line { display: flex; justify-content: flex-end; align-items: center; gap: 8px; }
  .contact svg { width: 13px; height: 13px; flex: none; }
</style>
</head>
<body>
<main class="stage">

  <section class="card card-back" aria-label="Card back">
    <div class="brand-name">Satchel &amp; Sundial</div>
    <div class="divider"></div>
    <p class="tagline">Live a life you don't need a holiday from</p>
  </section>

  <section class="card card-front" aria-label="Card front">
    <svg class="swoosh" viewBox="0 0 600 343" aria-hidden="true">
      <path d="M30,343 Q150,175 600,140 L600,158 Q175,192 58,343 Z" fill="var(--teal)"/>
      <path d="M58,343 Q175,192 600,158 L600,343 Z" fill="var(--ink)"/>
    </svg>
    <div class="brand-name">Satchel &amp; Sundial</div>
    <div class="contact">
      <div class="person">Dorota Falkner</div>
      <div class="role">Your Lifestyle Business Coach<br>Retreat &amp; Trip Leader</div>
      <div class="details">
        <div class="line">hello@satchelandsundial.example
          <svg viewBox="0 0 16 16" aria-hidden="true"><rect x="1" y="3" width="14" height="10" rx="1" fill="var(--teal)"/><path d="M1.5,3.5 L8,9 L14.5,3.5" fill="none" stroke="var(--ink)" stroke-width="1.3"/></svg>
        </div>
        <div class="line">www.satchelandsundial.example
          <svg viewBox="0 0 16 16" aria-hidden="true"><circle cx="8" cy="8" r="7" fill="var(--teal)"/><path d="M1,8 H15 M8,1 Q3,8 8,15 M8,1 Q13,8 8,15" fill="none" stroke="var(--ink)" stroke-width="1"/></svg>
        </div>
      </div>
    </div>
  </section>

</main>
</body>
</html>
```